Brell Stone Company Business Cards

Front and Back Business Card - logo and text setup - cool design. I need workable photoshop or illustrator files so I can setup each employee card with design that is created
Updates

Hi everyone, thank you for the great entries. Please no more white and blue cards - there are so many already - black and silver only now please. thanks!

Target Market(s)

Construction Industry - Facility Managers

Industry/Entity Type

Construction

Contact Information for Business Card

I really like contemporary simplistic looks - clean neat....not opposed to seeing some black backrounds

Requirements
Must have
• Logo/website address with design on front only - www.brellstone-example.com (logo attached)
• Back:
• Name/Title/Company Address/Phone/email address
Nice to have
• Cool design
Should not have
• Nothing gimmicky like Fire or Water - since we are a Fire Protection company - it has all been done

```html
<!DOCTYPE html>
<html lang="en">
<head>
<meta charset="UTF-8">
<title>Brell Stone Company Business Cards</title>
<link href="https://fonts.googleapis.com/css2?family=Open+Sans:ital,wght@0,400;0,600;0,800;1,700&display=swap" rel="stylesheet">
<style>
  :root {
    --page-bg: #1c1c1e;
    --card-bg: #050505;
    --brand-blue: #1c36c8;
    --brand-red: #ff2626;
    --icon-orange: #ff5a3a;
    --text-white: #f4f4f4;
    --divider: #5a5a5a;
  }
  * { margin: 0; padding: 0; box-sizing: border-box; }
  html, body {
    width: 1200px;
    height: 960px;
    overflow: hidden;
    background: var(--page-bg);
    font-family: "Open Sans", Arial, sans-serif;
  }
  .canvas {
    width: 1200px;
    height: 960px;
    display: flex;
    flex-direction: column;
    align-items: center;
    justify-content: center;
    gap: 70px;
  }
  .card {
    width: 640px;
    height: 366px;
    background: var(--card-bg);
    border-radius: 4px;
    box-shadow: 0 10px 30px rgba(0, 0, 0, 0.55);
    position: relative;
    color: var(--text-white);
    overflow: hidden;
  }
  .brand-name {
    font-weight: 800;
    color: var(--brand-blue);
    letter-spacing: -0.5px;
    line-height: 1;
    display: flex;
    align-items: center;
    gap: 12px;
    white-space: nowrap;
  }
  .brand-square {
    width: 16px;
    height: 16px;
    background: var(--brand-red);
    flex-shrink: 0;
  }

  /* Front */
  .card-front {
    display: flex;
    flex-direction: column;
    align-items: center;
    justify-content: center;
    gap: 40px;
  }
  .card-front .brand-name { font-size: 40px; }
  .front-website {
    font-size: 16px;
    letter-spacing: 4px;
  }

  /* Back */
  .card-back .brand-name {
    position: absolute;
    top: 64px;
    left: 50%;
    transform: translateX(-50%);
    font-size: 36px;
  }
  .contact-area {
    position: absolute;
    top: 160px;
    left: 0;
    right: 0;
    display: flex;
    justify-content: center;
  }
  .person-block {
    text-align: right;
    padding-right: 22px;
    font-size: 15px;
    line-height: 1.45;
  }
  .person-name, .person-title {
    font-weight: 700;
    font-style: italic;
    font-size: 16px;
  }
  .divider {
    width: 1px;
    background: var(--divider);
    height: 150px;
  }
  .contact-list {
    list-style: none;
    padding-left: 22px;
    padding-top: 40px;
    font-size: 15px;
  }
  .contact-list li {
    display: flex;
    align-items: center;
    gap: 10px;
    margin-bottom: 8px;
  }
  .contact-icon {
    width: 14px;
    height: 14px;
    flex-shrink: 0;
  }
</style>
</head>
<body>
<main class="canvas">
  <section class="card card-front" aria-label="Business card front">
    <div class="brand-name"><span class="brand-square"></span>Brell Stone Company</div>
    <div class="front-website">www.brellstone-example.com</div>
  </section>

  <section class="card card-back" aria-label="Business card back">
    <div class="brand-name"><span class="brand-square"></span>Brell Stone Company</div>
    <div class="contact-area">
      <div class="person-block">
        <div class="person-name">Dana Whitlock</div>
        <div class="person-title">President</div>
        <div class="address-line">48 Harbor Works Lane</div>
        <div class="address-line">Millbrook, NY 10000</div>
      </div>
      <div class="divider"></div>
      <ul class="contact-list">
        <li>
          <svg class="contact-icon" viewBox="0 0 24 24" aria-hidden="true">
            <path fill="var(--icon-orange)" d="M6.6 10.8a15.1 15.1 0 0 0 6.6 6.6l2.2-2.2a1 1 0 0 1 1-.25 11.4 11.4 0 0 0 3.6.57 1 1 0 0 1 1 1V20a1 1 0 0 1-1 1A17 17 0 0 1 3 4a1 1 0 0 1 1-1h3.5a1 1 0 0 1 1 1c0 1.25.2 2.45.57 3.570a1 1 0 0 1-.25 1z"/>
          </svg>
          <span>(555) 014-2290</span>
        </li>
        <li>
          <svg class="contact-icon" viewBox="0 0 24 24" aria-hidden="true">
            <rect x="2" y="5" width="20" height="14" rx="1" fill="var(--icon-orange)"/>
            <path d="M2.5 5.5 12 13l9.5-7.5" fill="none" stroke="var(--card-bg)" stroke-width="1.6"/>
          </svg>
          <span>info@brellstone-example.com</span>
        </li>
        <li>
          <svg class="contact-icon" viewBox="0 0 24 24" aria-hidden="true">
            <g fill="none" stroke="var(--icon-orange)" stroke-width="2">
              <circle cx="12" cy="12" r="9.5"/>
              <ellipse cx="12" cy="12" rx="4" ry="9.5"/>
              <path d="M2.5 12h19M4 7h16M4 17h16"/>
            </g>
          </svg>
          <span>www.brellstone-example.com</span>
        </li>
      </ul>
    </div>
  </section>
</main>
</body>
</html>
```